Young, dynamic furniture company needs a new business card design

We require a new business card design for our modern furniture company which supplies furniture and appliances to the property and development market.
Oakridge Interiors has become one of the leading furniture & appliance suppliers to the property market withing London. With over 10 years experience, we have increased our business to supply not only private landlords and managing agents, but also property developers, housing associations and local councils.
We offer not only a complete range of furniture which includes beds, wardrobes, dining sets and sofas, but also a high quality, full delivery and assembly service to help you with all our furnishing needs.

Target Market(s)

Private landlords, estate agents, letting agents, property management companies

Industry/Entity Type

Business

Contact Information for Business Card

Name,
Title,
Address,
Mobile,
Telephone,
Fax, Website, email address

Font styles to use
Sans Serif

Colors
3176b5
0555a3
85abd2
cfdeed

Requirements
Must have
• All the above information for each of our staff, along with our logo

```html
<!DOCTYPE html>
<html lang="en">
<head>
<meta charset="utf-8">
<title>Oakridge Interiors – Business Card</title>
<link rel="stylesheet" href="https://fonts.googleapis.com/css2?family=Roboto+Condensed:wght@400;700&display=swap">
<style>
  :root {
    --navy: #0555a3;
    --navy-deep: #1d3f8c;
    --blue: #3176b5;
    --blue-soft: #85abd2;
    --blue-pale: #cfdeed;
    --ink: #2a2a2a;
    --text: #5a5a5a;
    --paper: #ffffff;
    --stage: #e6e8ec;
  }
  * { margin: 0; padding: 0; box-sizing: border-box; }
  html, body { width: 1200px; height: 950px; overflow: hidden; }
  body {
    background: var(--stage);
    font-family: "Roboto Condensed", "Arial Narrow", sans-serif;
    position: relative;
  }
  .card {
    position: absolute;
    left: 250px;
    width: 700px;
    height: 400px;
    overflow: hidden;
    box-shadow: 0 6px 18px rgba(0,0,0,0.18);
  }

  /* Back side */
  .card-back { top: 50px; background: var(--navy-deep); color: var(--paper); }
  .card-back .brand {
    position: absolute; left: 0; right: 0; top: 150px; text-align: center;
  }
  .brand-name {
    font-weight: 400; font-size: 40px; letter-spacing: 1px; text-transform: uppercase;
    display: inline-flex; align-items: center; gap: 12px;
  }
  .brand-mark { width: 22px; height: 22px; background: currentColor; display: inline-block; }
  .brand-tagline {
    font-size: 15px; letter-spacing: 1.5px; text-transform: uppercase; margin-top: 6px;
  }
  .card-back .web {
    position: absolute; left: 0; right: 0; bottom: 70px; text-align: center;
    font-size: 18px; letter-spacing: 5px;
  }

  /* Front side */
  .card-front { top: 500px; background: var(--paper); }
  .card-front .bands { position: absolute; inset: 0; }
  .card-front .brand {
    position: absolute; left: 30px; width: 330px; top: 170px; text-align: center; color: var(--ink);
  }
  .card-front .brand-name { font-size: 32px; }
  .card-front .brand-mark { width: 18px; height: 18px; }
  .card-front .brand-tagline { font-size: 13px; }
  .divider {
    position: absolute; left: 385px; top: 70px; height: 260px; width: 1px; background: #d6d6d6;
  }
  .contact { position: absolute; left: 415px; top: 78px; color: var(--text); font-size: 16px; line-height: 1.35; }
  .person-name { color: var(--navy-deep); font-weight: 700; font-size: 24px; text-transform: uppercase; line-height: 1.1; }
  .person-title { color: var(--blue); font-size: 17px; text-transform: uppercase; margin-bottom: 6px; }
  .address { margin-bottom: 6px; }
  .contact-list { list-style: none; }
  .contact-list li { display: flex; align-items: center; gap: 10px; height: 23px; }
  .contact-list svg { width: 15px; height: 15px; fill: var(--navy-deep); flex: none; }
</style>
</head>
<body>

<section class="card card-back" aria-label="Card back">
  <div class="brand">
    <div class="brand-name"><span class="brand-mark"></span>Oakridge Interiors</div>
    <div class="brand-tagline">Trade Furniture Solutions</div>
  </div>
  <div class="web">www.oakridgeint.com</div>
</section>

<section class="card card-front" aria-label="Card front">
  <svg class="bands" viewBox="0 0 700 400" preserveAspectRatio="none" aria-hidden="true">
    <polygon points="360,0 700,0 700,40 520,40" fill="var(--blue)"/>
    <polygon points="0,345 700,290 700,400 0,400" fill="var(--navy-deep)"/>
    <polygon points="0,338 700,283 700,290 0,345" fill="var(--blue)"/>
  </svg>

  <div class="brand">
    <div class="brand-name"><span class="brand-mark"></span>Oakridge Interiors</div>
    <div class="brand-tagline">Trade Furniture Solutions</div>
  </div>

  <div class="divider"></div>

  <div class="contact">
    <div class="person-name">Daniel Marsh</div>
    <div class="person-title">President</div>
    <div class="address">2217 Hollis Lane<br>Millbrook, NY 11020</div>
    <ul class="contact-list">
      <li>
        <svg viewBox="0 0 24 24"><path d="M6.6 10.8a15.1 15.1 0 0 0 6.6 6.6l2.2-2.2a1 1 0 0 1 1-.25 11.4 11.4 0 0 0 3.6.57 1 1 0 0 1 1 1V20a1 1 0 0 1-1 1A17 17 0 0 1 3 4a1 1 0 0 1 1-1h3.5a1 1 0 0 1 1 1c0 1.25.2 2.45.57 3.57a1 1 0 0 1-.25 1z"/></svg>
        555 0142 3381
      </li>
      <li>
        <svg viewBox="0 0 24 24"><path d="M7 1h10a2 2 0 0 1 2 2v18a2 2 0 0 1-2 2H7a2 2 0 0 1-2-2V3a2 2 0 0 1 2-2zm0 3v14h10V4zm5 15.5a1 1 0 1 0 0 2 1 1 0 0 0 0-2z"/></svg>
        555 0187 2264
      </li>
      <li>
        <svg viewBox="0 0 24 24"><path d="M6 2h9l3 3v4h1a3 3 0 0 1 3 3v7h-4v3H6v-3H2v-7a3 3 0 0 1 3-3h1zm2 2v5h8V6h-2V4zm0 12v4h8v-4z"/></svg>
        555 0193 4470
      </li>
      <li>
        <svg viewBox="0 0 24 24"><path d="M2 5h20v14H2zm2 2v.5l8 5 8-5V7zm0 2.8V17h16V9.8l-8 5z"/></svg>
        daniel@oakridgeint.com
      </li>
      <li>
        <svg viewBox="0 0 24 24"><path d="M12 2a10 10 0 1 0 0 20 10 10 0 0 0 0-20zm6.9 9h-3a15 15 0 0 0-1.3-5.6A8 8 0 0 1 18.9 11zM12 4c.9 1.2 1.8 3.6 1.9 7h-3.8c.1-3.4 1-5.8 1.9-7zM9.4 5.4A15 15 0 0 0 8.1 11h-3a8 8 0 0 1 4.3-5.6zM5.1 13h3a15 15 0 0 0 1.3 5.6A8 8 0 0 1 5.1 13zm6.9 7c-.9-1.2-1.8-3.6-1.9-7h3.8c-.1 3.4-1 5.8-1.9 7zm2.6-1.4a15 15 0 0 0 1.3-5.6h3a8 8 0 0 1-4.3 5.6z"/></svg>
        www.oakridgeint.com
      </li>
    </ul>
  </div>
</section>

</body>
</html>
```